Social media app sign-up flow that asks users to give personal info and connect with other apps

Design an interactive, fun, and playful sign-up flow in which you are providing information about you, your interests, and connecting with different API plug-ins such as Chatterloop, Workvine, Tunevale, etc. (using the brand palette attached).

Basic wireframe, and business requirements are also attached.

Target Market(s)

Gen Z + Millennials (ages 22-40)

Font styles to use
Sans Serif

Colors
fbed22
fbee3d
fbf289

Requirements
Must have
• Forms for users to submit their info. Follow the color palette attached.

Connect with Chatterloop, Connect with Workvine, Connect with Tunevale, Connect with Gatherpost buttons
Nice to have
• I like the way you can use cards to submit your information for each category. Interactive card design for providing your info
Should not have
• Basic outdated designs, long forms

```html
<!DOCTYPE html>
<html lang="en">
<head>
<meta charset="utf-8">
<title>Sign-up flow</title>
<link rel="stylesheet" href="https://fonts.googleapis.com/css2?family=Montserrat:wght@400;500;600;700&display=swap">
<style>
  :root {
    --canvas: #e6e6e6;
    --panel-top: #5e6677;
    --panel-bottom: #262a32;
    --gold-start: #d1b778;
    --gold-end: #fcc12c;
    --card-border: #b39034;
    --white: #ffffff;
    --field-text: #3b3f48;
    --muted: #5b606b;
    --line: #c9ccd3;
    --tag-bg: #a7afbf;
    --tag-text: #f4f5f8;
    --suggest-bg: #252931;
  }
  * { box-sizing: border-box; margin: 0; padding: 0; }
  html, body { width: 1200px; height: 755px; overflow: hidden; }
  body {
    background: var(--canvas);
    font-family: "Montserrat", sans-serif;
    color: var(--white);
    position: relative;
  }
  .screen {
    position: absolute;
    top: 89px;
    width: 336px;
    height: 618px;
    background: linear-gradient(180deg, var(--panel-top), var(--panel-bottom));
  }
  .screen--signup { left: 59px; }
  .screen--about { left: 441px; }
  .screen--places { left: 805px; top: 90px; height: 617px; }
  .screen__title {
    position: absolute; left: 0; right: 0;
    text-align: center; font-weight: 500; line-height: 1;
    letter-spacing: 0.5px;
  }
  .screen--signup .screen__title { top: 30px; font-size: 29px; }
  .screen--about .screen__title { top: 40px; font-size: 25px; }
  .screen--places .screen__title { top: 44px; font-size: 23px; }

  /* Sign up */
  .field {
    position: absolute; left: 39px; width: 268px; height: 50px;
    background: var(--white); color: var(--field-text);
  }
  .field--country { top: 92px; padding: 11px 12px; }
  .field__label { font-size: 9px; color: var(--muted); display: block; }
  .field__value { font-size: 14px; font-weight: 600; display: block; margin-top: 2px; }
  .field__chevron { position: absolute; right: 17px; top: 20px; }
  .field--phone { top: 150px; padding: 0 14px; display: flex; align-items: center; font-size: 12px; color: var(--muted); }
  .hint { position: absolute; top: 210px; left: 0; right: 0; text-align: center; font-size: 9.5px; }
  .btn-primary {
    position: absolute; left: 39px; top: 233px; width: 268px; height: 44px;
    background: linear-gradient(90deg, var(--gold-start), var(--gold-end));
    display: flex; align-items: center; justify-content: center;
    font-size: 16px; font-weight: 700; letter-spacing: 0.3px;
  }
  .divider { position: absolute; top: 292px; left: 42px; width: 252px; display: flex; align-items: center; gap: 12px; font-size: 11px; font-weight: 600; }
  .divider::before, .divider::after { content: ""; flex: 1; height: 1px; background: var(--line); opacity: 0.6; }
  .option {
    position: absolute; left: 39px; width: 268px; height: 39px;
    border: 1px solid var(--line);
    display: flex; align-items: center;
    font-size: 10.5px; font-weight: 700;
  }
  .option__icon {
    width: 38px; height: 100%; border-right: 1px solid var(--line);
    display: flex; align-items: center; justify-content: center; flex: none;
  }
  .option__label { flex: 1; text-align: center; padding-right: 38px; }
  .dot { width: 10px; height: 10px; border-radius: 50%; background: var(--white); }
  .login-note { position: absolute; top: 522px; left: 0; right: 0; text-align: center; font-size: 10.5px; }
  .login-note a { color: var(--white); }

  /* About cards */
  .card {
    position: absolute; width: 131px; height: 105px;
    border: 1px solid var(--card-border);
    display: flex; align-items: center; justify-content: center;
    text-align: center; font-size: 13.5px; line-height: 1.3;
  }
  .card--active { background: linear-gradient(90deg, var(--gold-start), var(--gold-end)); border-color: transparent; }
  .col-a { left: 29px; } .col-b { left: 177px; }
  .row-1 { top: 97px; } .row-2 { top: 220px; } .row-3 { top: 342px; } .row-4 { top: 464px; }

  /* Places */
  .tag-field {
    position: absolute; left: 40px; top: 100px; width: 265px; height: 156px;
    border: 1px solid var(--card-border);
  }
  .tag {
    position: absolute; height: 24px; background: var(--tag-bg); color: var(--tag-text);
    font-size: 10px; display: flex; align-items: center; justify-content: center;
  }
  .tag__remove { position: absolute; top: 2px; right: 2px; }
  .suggestion {
    position: absolute; left: 17px; top: 111px; width: 132px; height: 24px;
    background: var(--suggest-bg); font-size: 8px; display: flex; align-items: center; padding-left: 12px;
  }
  .screen--places .option { left: 39px; width: 256px; font-size: 11px; }
</style>
</head>
<body>

<section class="screen screen--signup">
  <h1 class="screen__title">Sign Up</h1>
  <div class="field field--country">
    <span class="field__label">Country/Region</span>
    <span class="field__value">United State (+1)</span>
    <svg class="field__chevron" width="19" height="11" viewBox="0 0 19 11"><path d="M1 1l8.5 8.5L18 1" fill="none" stroke="#8a8e97" stroke-width="2"/></svg>
  </div>
  <div class="field field--phone">Phone Number</div>
  <p class="hint">Augiat in pede Fusce tellus Sed metus augue</p>
  <div class="btn-primary">Countinue</div>
  <div class="divider">or</div>

  <div class="option" style="top:326px">
    <span class="option__icon">
      <svg width="13" height="10" viewBox="0 0 13 10"><rect x="0" y="0" width="13" height="10" rx="1" fill="#fff"/><path d="M0.5 1l6 4.5 6-4.5" fill="none" stroke="#4a505c" stroke-width="1.2"/></svg>
    </span>
    <span class="option__label">Countinue with email</span>
  </div>
  <div class="option" style="top:371px">
    <span class="option__icon"><span class="dot"></span></span>
    <span class="option__label">Countinue with Chatterloop</span>
  </div>
  <div class="option" style="top:416px">
    <span class="option__icon"><span class="dot"></span></span>
    <span class="option__label">Countinue with Searchly</span>
  </div>
  <div class="option" style="top:461px">
    <span class="option__icon"><span class="dot"></span></span>
    <span class="option__label">Countinue with Orchardo</span>
  </div>
  <p class="login-note">Already have an account? <a href="#">Log in</a></p>
</section>

<section class="screen screen--about">
  <h1 class="screen__title">Tell me about you</h1>
  <div class="card card--active col-a row-1">Places<br>I've Lived</div>
  <div class="card col-b row-1">Schools<br>I've Attended</div>
  <div class="card col-a row-2">Place<br>I've Worked</div>
  <div class="card col-b row-2">People<br>I Know</div>
  <div class="card col-a row-3">Events<br>I've Attended</div>
  <div class="card col-b row-3">Events<br>I'm Attending</div>
  <div class="card col-a row-4">Music<br>I Love</div>
  <div class="card col-b row-4">Teams<br>I love</div>
</section>

<section class="screen screen--places">
  <h1 class="screen__title">Place I’ve Lived</h1>
  <div class="tag-field">
    <span class="tag" style="left:17px;top:24px;width:73px">Chicago
      <svg class="tag__remove" width="9" height="9" viewBox="0 0 9 9"><circle cx="4.5" cy="4.5" r="4.5" fill="#fff"/><path d="M2.8 2.8l3.4 3.4M6.2 2.8L2.8 6.2" stroke="#a7afbf" stroke-width="1"/></svg></span>
    <span class="tag" style="left:96px;top:24px;width:73px">Madrid
      <svg class="tag__remove" width="9" height="9" viewBox="0 0 9 9"><circle cx="4.5" cy="4.5" r="4.5" fill="#fff"/><path d="M2.8 2.8l3.4 3.4M6.2 2.8L2.8 6.2" stroke="#a7afbf" stroke-width="1"/></svg></span>
    <span class="tag" style="left:172px;top:24px;width:73px">Paris
      <svg class="tag__remove" width="9" height="9" viewBox="0 0 9 9"><circle cx="4.5" cy="4.5" r="4.5" fill="#fff"/><path d="M2.8 2.8l3.4 3.4M6.2 2.8L2.8 6.2" stroke="#a7afbf" stroke-width="1"/></svg></span>
    <span class="tag" style="left:18px;top:55px;width:98px;font-size:9px">Rio de Janiero
      <svg class="tag__remove" width="9" height="9" viewBox="0 0 9 9"><circle cx="4.5" cy="4.5" r="4.5" fill="#fff"/><path d="M2.8 2.8l3.4 3.4M6.2 2.8L2.8 6.2" stroke="#a7afbf" stroke-width="1"/></svg></span>
    <span class="tag" style="left:18px;top:87px;width:98px;height:23px;justify-content:flex-start;padding-left:13px">London</span>
    <div class="suggestion">London, United Kingdom</div>
  </div>
  <div class="option" style="top:280px">
    <span class="option__icon"><span class="dot"></span></span>
    <span class="option__label">Connect with Chatterloop</span>
  </div>
  <div class="option" style="top:334px">
    <span class="option__icon"><span class="dot"></span></span>
    <span class="option__label">Connect with Workvine</span>
  </div>
</section>

</body>
</html>
```